TalkHarbor - Language Coaching Services

Sleek, innovative, trendy design for Language Coaching business.

TalkHarbor is a new UK based company that provides Language Coaching services. We offer highly personalized on-line and face to face language courses. We also impart learning techniques workshops based on the latest neuroscience research for second-language acquisition.

Target Market(s)

See attached info

Industry/Entity Type

Consulting

Contact Information for Business Card

TalkHarbor
DaniaKV@talkharbor.co.uk
TalkHarbor.co.uk
London, UK

Font styles to use
Sans Serif

```html
<!DOCTYPE html>
<html lang="en">
<head>
<meta charset="utf-8">
<title>TalkHarbor – Business Card</title>
<link rel="stylesheet" href="https://fonts.googleapis.com/css2?family=Montserrat:wght@400;500&family=Lato:wght@400;700&display=swap">
<style>
  :root {
    --backdrop: #676767;
    --card-white: #ffffff;
    --brand-blue: #1793d1;
    --brand-blue-deep: #0a7fbf;
    --blue-light: #0aa6df;
    --text-grey: #555a5e;
    --white: #ffffff;
  }
  * { margin: 0; padding: 0; box-sizing: border-box; }
  html, body {
    width: 1200px; height: 900px; overflow: hidden;
    background: var(--backdrop);
  }
  .stage { position: relative; width: 1200px; height: 900px; }

  .card {
    position: absolute; top: 200px; width: 310px; height: 502px;
    box-shadow: 3px 4px 6px rgba(0,0,0,0.35);
  }
  .card-front {
    left: 253px; background: var(--card-white);
    border-radius: 62px 0 62px 3px;
  }
  .card-back {
    left: 627px;
    border-radius: 3px 62px 3px 62px;
    background: linear-gradient(160deg, var(--blue-light) 0%, var(--brand-blue) 55%, var(--brand-blue-deep) 100%);
    overflow: hidden;
  }
  .back-decoration { position: absolute; inset: 0; }

  .brand-mark {
    position: absolute; left: 108px; top: 85px;
    width: 92px; height: 92px; border-radius: 50%;
    border: 6px solid var(--brand-blue);
  }
  .wordmark {
    position: absolute; left: 0; width: 100%; text-align: center;
    font-family: "Montserrat", sans-serif; font-weight: 400;
    letter-spacing: 0.5px; white-space: nowrap;
  }
  .card-front .wordmark { top: 188px; font-size: 33px; color: var(--brand-blue); }
  .card-back .wordmark { top: 394px; font-size: 35px; color: var(--white); }
  .card-back .website {
    position: absolute; top: 450px; width: 100%; text-align: center;
    font-family: "Lato", sans-serif; font-weight: 700; font-size: 14px;
    letter-spacing: 0.6px; color: var(--white);
  }

  .contact {
    position: absolute; left: 33px; top: 311px;
    font-family: "Lato", sans-serif; color: var(--text-grey); font-size: 14px; line-height: 18px;
  }
  .person-name { font-family: "Montserrat", sans-serif; font-size: 16px; color: var(--brand-blue); letter-spacing: 0.3px; }
  .person-name strong { font-weight: 500; }
  .company { margin-top: 14px; font-family: "Montserrat", sans-serif; font-weight: 500; font-size: 14px; color: var(--brand-blue); }
  .details { list-style: none; margin-top: 14px; }
  .details li { display: flex; align-items: center; gap: 5px; }
  .details svg { width: 11px; height: 11px; fill: var(--brand-blue); flex: none; }
</style>
</head>
<body>
<main class="stage">
  <section class="card card-front">
    <div class="brand-mark"></div>
    <div class="wordmark">TALKHARBOR</div>
    <div class="contact">
      <div class="person-name"><strong>MARCUS</strong> HALE</div>
      <div>Managing Director</div>
      <div class="company">TALKHARBOR</div>
      <div>London, UK</div>
      <ul class="details">
        <li><svg viewBox="0 0 12 12"><path d="M2 0h8a1 1 0 0 1 1 1v10a1 1 0 0 1-1 1H2a1 1 0 0 1-1-1V1a1 1 0 0 1 1-1zm.5 1.5v7.5h7V1.5z"/></svg>044 777 1234</li>
        <li><svg viewBox="0 0 12 12"><path d="M0 2h12v8H0zm1 1v.4l5 3.2 5-3.2V3z"/></svg>DaniaKV@talkharbor.co.uk</li>
        <li><svg viewBox="0 0 12 12"><circle cx="6" cy="6" r="6"/><path d="M3 4c1 0 2 1 1.5 2S6 8 5 10M8 2c-.5 1 .5 2 1.5 2" stroke="#fff" stroke-width="1" fill="none"/></svg>www.TalkHarbor.co.uk</li>
      </ul>
    </div>
  </section>

  <section class="card card-back">
    <div class="back-decoration" role="img" aria-label="Soft blue background where the brand symbol appears as a large faint decoration"></div>
    <div class="wordmark">TALKHARBOR</div>
    <div class="website">www.TalkHarbor.co.uk</div>
  </section>
</main>
</body>
</html>
```